Mark Tolvane actor business cards

I need unique and interesting business cards that have my headshot photo, my name, tagline/position/skills, contact info, preferred pronouns (he, him, his), and social media handles. These need to be memorable networking tools to hand out at events that stand out. I am an actor that works in theatre, film, and TV and usually play darker dramatic roles, though it doesn't have to necessarily need to be reflected in the design, but I am not a light, comedic actor. In my email tagline, My position/skills are "Actor, storyteller, theatre maker."

Target Market(s)

Casting directors, film and television community, theatre community.

Industry/Entity Type

Performing Art

Contact Information for Business Card

Mark Tolvane. Pronouns: he, him, his. Contact info: (555)-318-7064, Marktolvane.example, marktolvane@postbox.example. Talent representation: Kirwood Talent Agency. Social Media: Facebook page, twitter and instagram: @MarkTolvanePlays. Company Member of Harbin Theatre Company.

Font styles to use
Serif
Decorative

Colors

Designer to choose colors to be used in the design.

Requirements
Must have
• Headshot photo, name, tagline, preferred pronouns, contact info, Social media handle, talent agency logo, harbin theatre company logo. Both logos should be smaller than my name. Under or near Harbin logo, it should say "Company Member"
Nice to have
• I would like to have the photo, my name, tagline, and maybe pronouns on one side, and all contact info, and social media, and talent agency logo on the other. I would like the style to reflect my type which is a little more serious and somewhat darker, and definitely not comedic.
Should not have
• No extraneous theatre lights, camera, or film, etc. clip art or photos. Use solid backgrounds or photos provided.

```html
<!DOCTYPE html>
<html lang="en">
<head>
<meta charset="utf-8">
<title>Mark Tolvane – Business Cards</title>
<link rel="stylesheet" href="https://fonts.googleapis.com/css2?family=Merienda:wght@400;700&family=Roboto:wght@400;500;700&display=swap">
<style>
  :root {
    --backdrop: #1e1e1e;
    --card-white: #ffffff;
    --ink: #111111;
    --ink-soft: #3a3a3a;
    --ink-muted: #6a6a6a;
    --accent-blue: #1ea7e8;
    --band-black: #050505;
    --photo-light: #c9d2dc;
    --photo-mid: #6f84a8;
    --photo-dark: #2c3140;
  }
  * { box-sizing: border-box; margin: 0; padding: 0; }
  html, body {
    width: 1200px; height: 1082px; overflow: hidden;
    background: var(--backdrop);
  }
  .canvas {
    position: relative; width: 1200px; height: 1082px;
    display: flex; justify-content: center; align-items: center; gap: 60px;
  }
  .card {
    position: relative; width: 400px; height: 700px;
    background: var(--card-white); overflow: hidden;
  }

  /* Front card */
  .agency-mark {
    position: absolute; top: 100px; left: 46px;
    display: flex; align-items: center; gap: 14px;
  }
  .agency-mark__dot {
    flex: none; width: 48px; height: 48px; border-radius: 50%;
    background: var(--accent-blue);
  }
  .agency-mark__name {
    font-family: "Merienda", serif; font-weight: 400;
    font-size: 28px; line-height: 1.15; color: var(--ink);
    width: 230px;
  }
  .identity {
    position: absolute; right: 40px; top: 318px; text-align: right;
  }
  .identity__name {
    font-family: "Merienda", serif; font-weight: 700;
    font-size: 36px; color: var(--ink); line-height: 1.1;
  }
  .identity__tagline {
    font-family: "Merienda", serif; font-weight: 400;
    font-size: 17px; color: var(--accent-blue); margin-top: 4px;
  }
  .identity__pronouns {
    font-family: "Roboto", sans-serif; font-weight: 400;
    font-size: 14px; color: var(--ink-muted); margin-top: 4px;
  }
  .contact {
    position: absolute; right: 40px; top: 446px; text-align: right;
    font-family: "Roboto", sans-serif; font-size: 16px; line-height: 1.5;
    color: var(--ink-soft);
  }
  .contact__label { font-weight: 700; color: var(--ink); }
  .social {
    position: absolute; right: 40px; top: 532px;
    display: flex; align-items: center; gap: 6px;
  }
  .social__dot {
    width: 28px; height: 28px; border-radius: 50%; background: var(--ink);
  }
  .social__handle {
    font-family: "Roboto", sans-serif; font-weight: 500;
    font-size: 15px; color: var(--ink); margin-right: 6px;
  }
  .company {
    position: absolute; left: 40px; right: 40px; bottom: 34px;
    display: flex; align-items: center; justify-content: flex-end; gap: 10px;
    border-top: 1px solid #dddddd; padding-top: 18px;
    font-family: "Roboto", sans-serif; text-align: right;
  }
  .company__square {
    flex: none; width: 30px; height: 30px; background: var(--ink);
  }
  .company__name {
    font-size: 15px; font-weight: 500; color: var(--ink);
  }
  .company__role {
    font-size: 13px; font-weight: 400; color: var(--accent-blue);
    text-transform: uppercase; letter-spacing: 0.5px; margin-top: 2px;
  }

  /* Back card */
  .headshot {
    position: absolute; inset: 0 0 140px 0;
    background: linear-gradient(180deg, var(--photo-light) 0%, var(--photo-light) 18%, #b89a86 34%, var(--photo-mid) 62%, var(--photo-dark) 100%);
  }
  .representation {
    position: absolute; left: 0; right: 0; bottom: 0; height: 140px;
    background: var(--band-black);
    padding: 40px 0 0 56px;
    font-family: "Roboto", sans-serif;
  }
  .representation__title {
    color: var(--accent-blue); font-weight: 700; font-size: 20px;
    letter-spacing: 0.5px; text-transform: uppercase;
  }
  .representation__agency {
    color: var(--card-white); font-weight: 400; font-size: 17px; margin-top: 4px;
  }
</style>
</head>
<body>
<main class="canvas">
  <section class="card card--front">
    <div class="agency-mark">
      <span class="agency-mark__dot"></span>
      <span class="agency-mark__name">Kirwood Talent Agency</span>
    </div>
    <div class="identity">
      <h1 class="identity__name">Mark Tolvane</h1>
      <p class="identity__tagline">Actor, storyteller, theatre maker</p>
      <p class="identity__pronouns">he / him / his</p>
    </div>
    <div class="contact">
      <p><span class="contact__label">Phone:</span> (555)-318-7064</p>
      <p><span class="contact__label">Email:</span> marktolvane@postbox.example</p>
      <p><span class="contact__label">Web:</span> Marktolvane.example</p>
    </div>
    <div class="social" aria-label="Social media">
      <span class="social__handle">@MarkTolvanePlays</span>
      <span class="social__dot"></span>
      <span class="social__dot"></span>
      <span class="social__dot"></span>
    </div>
    <div class="company">
      <div>
        <p class="company__name">Harbin Theatre Company</p>
        <p class="company__role">Company Member</p>
      </div>
      <span class="company__square"></span>
    </div>
  </section>

  <section class="card card--back">
    <div class="headshot" role="img" aria-label="Headshot of the actor in a blue shirt over a dark tee, on a white background"></div>
    <div class="representation">
      <p class="representation__title">Talent Representation</p>
      <p class="representation__agency">Kirwood Talent Agency.</p>
    </div>
  </section>
</main>
</body>
</html>
```